Professional Website for Leading Global Private Equity Real Estate Company

The company is a leading global Private Equity Real Estate (PERE). We need a homepage design, an inner page design, and color/font tweaks to the logo (color should be more soothing than current blue used in the logo). The logo website should project the company as global, professional, experienced, trustworthy, accessible, YOUNG, DYNAMIC, hi-tech. PLEASE SEE the attached Design Brief Word Doc for details.

Target Market(s)

institional investors and wealthy private individuals

Industry/Entity Type

Finance

Number of Pages Required

2 page

Font styles to use
Sans Serif
Other font styles liked:
• either like in https://www.ferndalequay.com/ or like in presentations (Montserrat Black & Montserrat Light, Century Gothic, Blair ITC, Almoni Neue DL 4.0 AAA Medium, Almoni DL AAA)

Requirements
Must have
• new color palette that is NOT based on current logo. they want a more soothing color palette than the blue in that logo. the new color palette should project: global, professional, experienced, trustworthy, accessible, YOUNG, DYNAMIC, hi-tech.
Nice to have
• the likes these sites: https://www.ferndalequay.com/ and https://www.tvr.law/

```html
<!DOCTYPE html>
<html lang="en">
<head>
<meta charset="utf-8">
<title>Meridane Real Estate</title>
<link href="https://fonts.googleapis.com/css2?family=Montserrat:wght@300;400;500;600;700;800&family=Work+Sans:wght@400;500&display=swap" rel="stylesheet">
<style>
:root{
  --navy:#1b3358;
  --navy-deep:#15294a;
  --gold:#c8841b;
  --ink:#1e2b3c;
  --text:#3d4757;
  --mute:#7b8492;
  --light:#f2f2f3;
  --grey:#e8e8e9;
  --white:#ffffff;
  --line:#c5ccd6;
}
*{box-sizing:border-box;margin:0;padding:0}
html,body{width:1200px;height:4267px;overflow:hidden}
body{position:relative;font-family:"Work Sans",sans-serif;color:var(--text);background:var(--white)}
.abs{position:absolute}
.display{font-family:"Montserrat",sans-serif}
.btn{position:absolute;display:flex;align-items:center;justify-content:center;font-family:"Montserrat",sans-serif;font-weight:600;font-size:13px;letter-spacing:1.5px;text-transform:uppercase;color:var(--white);background:var(--gold)}
.title{font-family:"Montserrat",sans-serif;font-size:36px;color:var(--ink);letter-spacing:1px;line-height:1.05}
.title b{font-weight:800}
.title span{font-weight:300}
.rule{width:56px;height:3px;background:var(--navy)}

/* hero */
.hero{top:0;left:0;width:1200px;height:698px;background:linear-gradient(120deg,#2a3a4f 0%,#4b5d72 35%,#7d8ea0 60%,#55677d 100%)}
.hero-shade{top:0;left:0;width:1200px;height:698px;background:linear-gradient(90deg,rgba(20,30,45,.55),rgba(20,30,45,.05))}
.nav{top:34px;left:0;width:1200px;height:24px}
.brand{left:103px;top:-14px;display:flex;align-items:center;gap:12px;color:var(--white);font-family:"Montserrat",sans-serif}
.brand i{width:48px;height:48px;border-radius:50%;background:var(--white);display:block}
.brand div{line-height:1.05}
.brand strong{display:block;font-weight:700;font-size:22px;letter-spacing:3px}
.brand small{font-size:18px;font-weight:300;letter-spacing:1px}
.menu{left:0;top:4px;width:1200px;height:16px;font-family:"Montserrat",sans-serif;font-size:11.5px;font-weight:500;color:var(--white);letter-spacing:.3px}
.menu span{position:absolute;top:0;white-space:nowrap}
.login{left:1008px;top:-5px;width:104px;height:34px;border:1.5px solid var(--white);color:var(--white);font-family:"Montserrat",sans-serif;font-size:12px;display:flex;align-items:center;justify-content:center}
.eyebrow{left:129px;top:234px;color:var(--white);font-family:"Montserrat",sans-serif;font-size:17px;letter-spacing:4px;font-weight:500}
.hero-title{left:127px;top:266px;color:var(--white);font-family:"Montserrat",sans-serif;font-weight:500;font-size:42px;line-height:41px;letter-spacing:3px;white-space:nowrap}
.play{left:770px;top:265px}
.scroll{left:0;width:1200px;top:622px;text-align:center;color:var(--white);font-family:"Montserrat",sans-serif;font-size:11px;letter-spacing:2px}

/* about */
.about{top:698px;left:0;width:1200px;height:594px;background:var(--light)}
.about-disc{left:170px;top:60px;width:380px;height:380px;border-radius:50%;background:#e7e7e9}
.dots{left:388px;top:320px;width:188px;height:190px;background-image:radial-gradient(#9aa3ae 1px,transparent 1.3px);background-size:8px 8px}
.stat{position:absolute;width:199px;height:159px;background:var(--white);box-shadow:0 8px 24px rgba(0,0,0,.08);padding:42px 32px;font-family:"Montserrat",sans-serif}
.stat b{display:block;font-size:30px;font-weight:600;color:var(--navy);letter-spacing:1px}
.stat small{display:block;margin-top:10px;font-size:13px;letter-spacing:1.5px;color:var(--mute);line-height:1.3}
.stat.dark{background:var(--navy)}
.stat.dark b,.stat.dark small{color:var(--white)}
.about-copy{left:660px;top:130px;width:430px}
.about-copy p,.edge p,.resp p{font-size:15px;line-height:28px}

/* platforms */
.platforms{top:1292px;left:0;width:1200px;height:524px}
.kicker{width:1200px;text-align:center;font-family:"Montserrat",sans-serif;font-size:13px;letter-spacing:3px;color:var(--mute)}
.tile{position:absolute;top:179px;height:241px;width:220px;overflow:hidden}
.tile .lbl{position:absolute;bottom:22px;width:100%;text-align:center;color:var(--white);font-family:"Montserrat",sans-serif;font-size:13px;font-weight:600;letter-spacing:1px;line-height:16px}
.tile.active{top:164px;height:271px;background:#2c3644;padding:70px 18px 0;text-align:center;color:var(--white)}
.tile.active h3{font-family:"Montserrat",sans-serif;font-size:15px;font-weight:600;letter-spacing:1px;line-height:17px}
.tile.active p{font-size:10.5px;line-height:18px;margin-top:10px;color:#d5d9e0}
.tile.active .btn{position:relative;margin:14px auto 0;width:121px;height:29px;font-size:10px}

/* edge */
.edge{top:1816px;left:0;width:1200px;height:525px;background:var(--navy)}
.edge .title{color:var(--white)}
.edge .rule{background:var(--white)}
.edge p{color:var(--white);font-size:16px}

/* newsletter */
.news{top:2341px;left:0;width:1200px;height:318px;background:var(--grey)}
.field{position:absolute;background:var(--white);border:1.5px solid #cfd3d8;font-size:12px;color:var(--mute);display:flex;align-items:center;padding-left:20px;font-family:"Montserrat",sans-serif}

/* responsibility */
.resp-frame{left:409px;top:2731px;width:723px;height:535px;border:2px solid var(--line)}
.btn.ghost{background:transparent;border:1.5px solid var(--gold);color:var(--gold)}

/* contact */
.contact{top:3377px;left:0;width:1200px;height:525px;background:linear-gradient(180deg,#1d3660 0%,#253f69 55%,#304c78 75%,#1f375e 100%)}
.contact .field{border:none;color:#55606e;font-size:13px;padding-left:16px;gap:10px}

/* footer */
.foot-h{font-family:"Montserrat",sans-serif;font-size:13px;font-weight:600;letter-spacing:1px;color:var(--navy)}
.foot-list{font-size:12.5px;color:var(--navy);line-height:27.3px}
.social{display:flex;gap:6px}
.social i{width:26px;height:26px;border-radius:50%;background:var(--navy);display:block}
</style>
</head>
<body>

<!-- HERO -->
<section class="abs hero" role="img" aria-label="Photo of business people meeting around laptops in a glass office"></section>
<div class="abs hero-shade"></div>
<header class="abs nav">
  <div class="abs brand"><i></i><div><strong>MERIDANE</strong><small>REAL ESTATE</small></div></div>
  <nav class="abs menu">
    <span style="left:414px">ABOUT US ⌄</span>
    <span style="left:514px">OUR BUSINESSES ⌄</span>
    <span style="left:660px">INVESTORS LOBBY</span>
    <span style="left:810px">NEWS</span>
    <span style="left:888px">CONTACT US</span>
  </nav>
  <div class="abs login">LOG IN</div>
</header>
<div class="abs eyebrow">MERIDANE REAL ESTATE</div>
<h1 class="abs hero-title">LEADING GLOBAL<br>PRIVATE EQUITY<br>REAL ESTATE</h1>
<div class="btn" style="left:129px;top:408px;width:176px;height:43px">About Us</div>
<svg class="abs play" width="100" height="100" viewBox="0 0 100 100"><circle cx="50" cy="50" r="48" fill="none" stroke="rgba(255,255,255,.5)" stroke-width="2"/><circle cx="50" cy="50" r="40" fill="#fff"/><path d="M42 34 L64 50 L42 66Z" fill="#111"/></svg>
<div class="abs scroll">SCROLL DOWN<br><svg width="20" height="14" viewBox="0 0 20 14"><path d="M3 3 L10 10 L17 3" fill="none" stroke="#fff" stroke-width="2.5"/></svg></div>

<!-- ABOUT -->
<section class="abs about">
  <div class="abs about-disc"></div>
  <div class="abs dots"></div>
  <div class="stat dark" style="left:134px;top:107px"><b>$120B</b><small>CREDIT &amp;<br>INSURANCE</small></div>
  <div class="stat" style="left:355px;top:162px"><b>$250</b><small>REAL ESTATE<br>PROJECTS</small></div>
  <div class="stat" style="left:134px;top:280px"><b>$250</b><small>PRIVATE EQUITY</small></div>
  <div class="stat" style="left:355px;top:333px"><b>$12B</b><small>FUND<br>SOLUTIONS</small></div>
  <div class="abs about-copy">
    <h2 class="title"><b>ABOUT MERIDANE</b><br><span>REAL ESTATE</span></h2>
    <div class="rule" style="margin:14px 0 24px"></div>
    <p>Lorem ipsum dolor sit amet, consectetur adipiscing elit, sed do eiusmod tempor incididunt ut labore et DoloreUt enim ad minim veniam, quis nostrud exercitation ullam-coea Lorem ipsum dolor sit amet, consectetur adipiscin-gLorem ipsum dolor sit.n ullamcoea</p>
  </div>
  <div class="btn" style="left:661px;top:406px;width:159px;height:39px;font-size:12px">Learn More</div>
</section>

<!-- PLATFORMS -->
<section class="abs platforms">
  <div class="abs kicker" style="top:60px">SERVICES PLATFORM</div>
  <h2 class="abs title" style="width:1200px;text-align:center;top:88px;font-size:34px"><b>OUR INVESTMENT</b> <span>PLATFORMS</span></h2>
  <div class="tile" style="left:45px;background:linear-gradient(170deg,#c9d6e6,#4a6685 55%,#1f2f44)" role="img" aria-label="Photo of a glass office tower against the sky"><div class="lbl">LOREM IPSUM<br>DOLOR SIT</div></div>
  <div class="tile active" style="left:273px"><h3>LOREM IPSUM<br>DOLOR SIT</h3><p>Lorem ipsum dolor sit amet, consectetur adipiscing elit, sed do eiusmod tempor</p><div class="btn">Learn More</div></div>
  <div class="tile" style="left:499px;background:linear-gradient(160deg,#dfe6ee,#5b6c7f 45%,#1a222d)" role="img" aria-label="Photo looking up at dark skyscrapers"><div class="lbl">LOREM IPSUM<br>DOLOR SIT</div></div>
  <div class="tile" style="left:727px;background:linear-gradient(170deg,#a9c4e0,#e6edf4 40%,#3e5e80)" role="img" aria-label="Photo of a glass tower under cloudy sky"><div class="lbl">LOREM IPSUM<br>DOLOR SIT</div></div>
  <div class="tile" style="left:949px;background:linear-gradient(150deg,#2a1b2c,#7b3654 50%,#1e1a2a)" role="img" aria-label="Photo of a building facade with lit windows at dusk"><div class="lbl">LOREM IPSUM<br>DOLOR SIT</div></div>
</section>

<!-- EDGE -->
<section class="abs edge">
  <svg class="abs" style="left:0;top:0" width="1200" height="525" viewBox="0 0 1200 525">
    <polygon points="701,0 1200,0 1200,525 693,525 565,255" fill="#3d6593"/>
    <polygon points="701,0 1200,0 1200,525 714,525 590,255" fill="#8fa4bd" role="img" aria-label="Aerial photo of a dense city skyline"/>
  </svg>
  <div class="abs" style="left:129px;top:92px;width:420px">
    <h2 class="title" style="font-size:37px"><b>OUR</b> <span>EDGE</span></h2>
    <div class="rule" style="margin:16px 0 26px;width:64px"></div>
    <p>Lorem ipsum dolor sit amet, consectetur adipiscing elit, sed do eiusmod tempor incididunt ut co laboris nisi ut aliquip ex ea commodo consequat.</p>
    <p style="margin-top:12px">Aabor et dolore magna aliqua. Ut enim ad minim veniam, quis nostrud exercitation</p>
  </div>
  <div class="btn" style="left:129px;top:353px;width:265px;height:50px">Investor Information</div>
</section>

<!-- NEWSLETTER -->
<section class="abs news">
  <h2 class="abs title" style="width:1200px;text-align:center;top:72px;font-size:34px"><b>STAY</b> <span>UPDATED</span></h2>
  <p class="abs" style="width:1200px;text-align:center;top:125px;font-size:16px">Get our latest insights, firm announcements and Charitable Foundation updates.</p>
  <div class="field" style="left:191px;top:176px;width:304px;height:51px">NAME*</div>
  <div class="field" style="left:505px;top:176px;width:305px;height:51px">EMAIL*</div>
  <div class="btn" style="left:820px;top:176px;width:196px;height:51px;font-size:15px">Subscribe</div>
</section>

<!-- RESPONSIBILITY -->
<div class="abs resp-frame"></div>
<div class="abs" style="left:113px;top:2779px;width:475px;height:442px;background:linear-gradient(135deg,#6b5a45,#b89466 45%,#3f3a35)" role="img" aria-label="Photo of a team gathered around a laptop in an office"></div>
<div class="abs resp" style="left:655px;top:2848px;width:440px">
  <h2 class="title" style="font-size:34px"><b>OUR</b> <span>RESPONSIBILITY</span></h2>
  <div class="rule" style="margin:14px 0 22px"></div>
  <p>Lorem ipsum dolor sit amet, consectetur adipiscing elit, sed do eiusmod tempor incididunt ut co laboris nisi ut al-iquip ex ea commodo consequat.</p>
  <p style="margin-top:12px">Aabor et dolore magna aliqua. Ut enim ad minim veniam, quis nostrud exercitation ullamco laboris &nbsp;et dolore</p>
</div>
<div class="btn ghost" style="left:650px;top:3099px;width:265px;height:51px">Investor Information</div>

<!-- CONTACT -->
<section class="abs contact" role="img" aria-label="Dark blue photo of snowy mountain ridges">
  <div class="abs kicker" style="left:119px;top:118px;width:auto;text-align:left;color:var(--white);font-size:15px;letter-spacing:4px">CONTACT US</div>
  <h2 class="abs display" style="left:115px;top:144px;color:var(--white);font-size:37px;line-height:38px;letter-spacing:1px"><b style="font-weight:800">GET IN TOUCH</b><br><span style="font-weight:300">WITH US</span></h2>
  <div class="field" style="left:480px;top:104px;width:276px;height:49px">
    <svg width="14" height="14" viewBox="0 0 14 14"><circle cx="7" cy="4.5" r="3" fill="none" stroke="#8a94a2"/><path d="M1.5 13c1-4 10-4 11 0" fill="none" stroke="#8a94a2"/></svg>First Name</div>
  <div class="field" style="left:764px;top:104px;width:277px;height:49px">
    <svg width="14" height="14" viewBox="0 0 14 14"><circle cx="7" cy="4.5" r="3" fill="none" stroke="#8a94a2"/><path d="M1.5 13c1-4 10-4 11 0" fill="none" stroke="#8a94a2"/></svg>Last Name</div>
  <div class="field" style="left:480px;top:162px;width:276px;height:48px">
    <svg width="14" height="14" viewBox="0 0 14 14"><path d="M2 1.5l3 0 1 3-2 1.5c1 2 2.5 3.5 4.5 4.5L10 8.5l3 1v3C7 13 1 7 2 1.5z" fill="none" stroke="#8a94a2"/></svg>Phone Number</div>
  <div class="field" style="left:764px;top:162px;width:277px;height:48px">
    <svg width="15" height="12" viewBox="0 0 15 12"><rect x="1" y="1" width="13" height="10" fill="none" stroke="#8a94a2"/><path d="M1 1l6.5 5L14 1" fill="none" stroke="#8a94a2"/></svg>Email address</div>
  <div class="field" style="left:480px;top:219px;width:561px;height:116px;align-items:flex-start;padding-top:14px;padding-left:22px">Message</div>
  <div class="btn" style="left:482px;top:348px;width:209px;height:50px;background:transparent;border:2px solid #cfd6e0;font-size:14px;letter-spacing:.5px">Submit Message</div>
</section>

<!-- FOOTER -->
<footer>
  <div class="abs foot-h" style="left:128px;top:3955px">IMPORTANT LINKS</div>
  <div class="abs foot-list" style="left:127px;top:3984px">About Us<br>Our Businesses<br>Investor Lobby<br>News<br>Contact Us</div>
  <div class="abs" style="left:323px;top:3948px;width:1px;height:195px;background:var(--line)"></div>
  <div class="abs foot-h" style="left:374px;top:3955px">EXPLORE MERIDANE REAL ESTATE</div>
  <div class="abs foot-list" style="left:375px;top:3984px">Private Equity<br>Real Estate<br>Credit<br>Strategic Partners<br>Tactical Opportunities<br>Infrastructure</div>
  <div class="abs foot-list" style="left:578px;top:3984px">Insurance Solutions<br>Life Sciences<br>Portfolio Operations<br>Technology and Innovations<br>Registered Products</div>
  <div class="abs" style="left:800px;top:3948px;width:1px;height:195px;background:var(--line)"></div>
  <div class="abs foot-h" style="left:850px;top:3955px">CONTACT DETAILS</div>
  <svg class="abs" style="left:850px;top:3988px" width="26" height="120" viewBox="0 0 26 120">
    <circle cx="13" cy="13" r="13" fill="#1b3358"/><path d="M13 6a5 5 0 0 1 5 5c0 4-5 9-5 9s-5-5-5-9a5 5 0 0 1 5-5z" fill="#fff"/><circle cx="13" cy="11" r="1.8" fill="#1b3358"/>
    <circle cx="13" cy="61" r="13" fill="#1b3358"/><path d="M8 54h3l1 3-1.5 1.2c.8 1.6 2 2.8 3.5 3.6L15 60.5l3 1v3c-5.5.5-11-5-10-10.5z" fill="#fff"/>
    <circle cx="13" cy="104" r="13" fill="#1b3358"/><rect x="7" y="99" width="12" height="9" fill="#fff"/><path d="M7 99l6 5 6-5" fill="none" stroke="#1b3358" stroke-width="1.2"/>
  </svg>
  <div class="abs foot-list" style="left:894px;top:3986px;line-height:16px">48 Harbor Crest Ave Suite B<br><span style="font-size:11px">Port Avalon, FL 33990</span></div>
  <div class="abs foot-list" style="left:894px;top:4036px;font-weight:500;font-size:14px">555-214-7780</div>
  <div class="abs foot-list" style="left:894px;top:4072px">info@meridanerealestate.com</div>
  <div class="abs social" style="left:859px;top:4123px"><i></i><i></i><i></i><i></i></div>
  <div class="abs" style="left:0;top:4190px;width:1200px;height:1px;background:#dde1e6"></div>
  <div class="abs" style="left:120px;top:4214px;font-size:11.5px;color:var(--navy)">Copyright © 2022 Meridane Realestate</div>
  <div class="abs" style="left:836px;top:4214px;font-size:11.5px;color:var(--navy)">Terms of Use &nbsp;| &nbsp;Sitemap &nbsp;| &nbsp;Privacy Policy</div>
</footer>

</body>
</html>
```